We need a new business card that reflects who we are. Professional, classy, modern, and service ori

We need a business card design for a window coverings design company in Kansas City called Bright Lane Interiors. We offer professional, modern, and high quality window covering products. We are looking to portray an image of a big, national franchise. We are a 5 location (with showrooms) business with 10 professional designers and 4 professional installers. These cards will be used with Thank you cards, given to realtors, and asked for referrals with.

Target Market(s)

Kansas City

Industry/Entity Type

Business

Contact Information for Business Card

We would like our card to look clean and simple on the front, featuring our logo and Marlow Fenwick's. Our designers' phone numbers and emails should be displayed as well as their title.

Font styles to use
Sans Serif

Colors

Designer to choose colors to be used in the design.

Requirements
Must have
• Front - Logos, name, phone number, email address
• Back - Showroom locations, social media? Appt date/time?
Nice to have
• I would like a clean and modern look (not contemporary. I like a white background, but I am open to ideas. Looking for a "National chain" look for a small business.
Should not have
• Too much busyness.

```html
<!DOCTYPE html>
<html lang="en">
<head>
<meta charset="utf-8">
<title>Bright Lane Interiors – Business Card</title>
<link rel="stylesheet" href="https://fonts.googleapis.com/css2?family=Roboto:wght@400;500;700&family=Roboto+Condensed:wght@400;700&display=swap">
<style>
  :root {
    --backdrop: #e6e4e2;
    --card: #f4f4f3;
    --red: #c44041;
    --ink: #1b1b1b;
    --text: #444444;
    --grey: #9a9ea1;
    --slate: #5d6a73;
    --rule: #c9c9c9;
  }
  * { margin: 0; padding: 0; box-sizing: border-box; }
  html, body { width: 1200px; height: 960px; overflow: hidden; }
  body { background: var(--backdrop); position: relative; font-family: "Roboto", sans-serif; }

  .card {
    position: absolute; width: 600px; height: 343px;
    background: var(--card); overflow: hidden;
    box-shadow: 0 3px 8px rgba(0,0,0,.25);
  }
  .card--front { left: 314px; top: 113px; }
  .card--back { left: 311px; top: 472px; }

  /* Front */
  .brand { position: absolute; left: 40px; top: 150px; width: 245px; text-align: center; }
  .brand__name {
    display: flex; align-items: center; justify-content: center; gap: 7px;
    font-family: "Roboto Condensed", sans-serif; font-weight: 700;
    font-size: 23px; color: var(--ink); letter-spacing: .3px;
  }
  .brand__mark { width: 13px; height: 13px; background: var(--red); }
  .brand__tagline {
    margin-top: 8px; font-family: "Roboto Condensed", sans-serif;
    font-size: 12.5px; color: var(--ink);
  }
  .divider { position: absolute; left: 305px; top: 107px; width: 1px; height: 130px; background: var(--rule); }

  .person { position: absolute; left: 333px; top: 103px; }
  .person__name {
    font-family: "Roboto Condensed", sans-serif; font-weight: 700;
    font-size: 25px; color: var(--red); line-height: 1.1;
  }
  .person__title {
    font-family: "Roboto", sans-serif; font-weight: 700;
    font-size: 14.5px; color: var(--ink); margin-top: 1px;
  }
  .contact { position: absolute; left: 333px; top: 178px; list-style: none; }
  .contact li {
    display: flex; align-items: center; gap: 8px;
    font-size: 14.5px; color: var(--text); height: 19.5px;
  }
  .contact svg { width: 13px; height: 13px; fill: var(--red); flex: none; }
  .footer-band { position: absolute; left: 0; top: 0; width: 600px; height: 343px; }

  /* Back */
  .partner {
    position: absolute; left: 0; top: 40px; width: 600px;
    display: flex; justify-content: center; align-items: center; gap: 7px;
    font-family: "Roboto Condensed", sans-serif; font-weight: 700;
    font-size: 14.5px; color: var(--slate);
  }
  .partner__mark { width: 10px; height: 10px; background: var(--slate); }

  .appointments { position: absolute; left: 82px; top: 80px; list-style: none; }
  .appointments li {
    display: flex; align-items: baseline; height: 45.5px;
    font-family: "Roboto Condensed", sans-serif; color: var(--red);
  }
  .appointments .label { font-size: 17px; }
  .appointments .fill { border-bottom: 1px dotted #777; height: 1px; margin: 0 4px; transform: translateY(-3px); }
  .fill--date { width: 166px; }
  .fill--time { width: 104px; }
  .appointments .meridiem { font-size: 13px; margin-left: 4px; }

  .locations { position: absolute; left: 0; top: 260px; width: 600px; text-align: center; }
  .locations__title {
    font-family: "Roboto Condensed", sans-serif; font-weight: 700;
    font-size: 15px; color: var(--red);
  }
  .locations__list {
    font-family: "Roboto Condensed", sans-serif; font-size: 13.5px;
    color: var(--text); margin-top: 3px;
  }
  .social { display: flex; justify-content: center; gap: 3px; margin-top: 6px; }
  .social span { width: 20px; height: 20px; border-radius: 50%; background: var(--red); }
</style>
</head>
<body>

<section class="card card--front">
  <div class="brand">
    <div class="brand__name"><span class="brand__mark"></span>Bright Lane Interiors</div>
    <div class="brand__tagline">Blinds, Shades, Shutters, Draperies &amp; Decor</div>
  </div>
  <div class="divider"></div>

  <div class="person">
    <div class="person__name">EVAN HALE</div>
    <div class="person__title">DESIGNER</div>
  </div>
  <ul class="contact">
    <li><svg viewBox="0 0 24 24"><path d="M6.6 10.8c1.4 2.8 3.8 5.1 6.6 6.6l2.2-2.2c.3-.3.7-.4 1-.2 1.1.4 2.3.6 3.6.6.6 0 1 .4 1 1V20c0 .6-.4 1-1 1C10.6 21 3 13.4 3 4c0-.6.4-1 1-1h3.5c.6 0 1 .4 1 1 0 1.3.2 2.5.6 3.6.1.3 0 .7-.2 1L6.6 10.8z"/></svg>913.555.0148</li>
    <li><svg viewBox="0 0 24 24"><path d="M2 6.5l10 6.5 10-6.5V19H2z M2 5h20l-10 6.5z"/></svg>info@brightlaneinteriors.com</li>
    <li><svg viewBox="0 0 24 24"><circle cx="12" cy="12" r="10"/><path d="M2 12h20M12 2c3 3 3 17 0 20M12 2c-3 3-3 17 0 20" stroke="#f4f4f3" stroke-width="1.5" fill="none"/></svg>brightlaneinteriors.com</li>
  </ul>

  <svg class="footer-band" viewBox="0 0 600 343" aria-hidden="true">
    <path d="M0,318 C200,300 400,330 600,306 L600,343 L0,343 Z" fill="var(--red)"/>
    <path d="M0,308 C200,290 400,320 600,296" fill="none" stroke="var(--grey)" stroke-width="2"/>
  </svg>
</section>

<section class="card card--back">
  <div class="partner"><span class="partner__mark"></span><span>Marlow Fenwick Gallery</span></div>

  <ul class="appointments">
    <li><span class="label">Date :</span><span class="fill fill--date"></span><span class="label">Time :</span><span class="fill fill--time"></span><span class="meridiem">AM/PM</span></li>
    <li><span class="label">Date :</span><span class="fill fill--date"></span><span class="label">Time :</span><span class="fill fill--time"></span><span class="meridiem">AM/PM</span></li>
    <li><span class="label">Date :</span><span class="fill fill--date"></span><span class="label">Time :</span><span class="fill fill--time"></span><span class="meridiem">AM/PM</span></li>
    <li><span class="label">Date :</span><span class="fill fill--date"></span><span class="label">Time :</span><span class="fill fill--time"></span><span class="meridiem">AM/PM</span></li>
  </ul>

  <div class="locations">
    <div class="locations__title">SHOWROOM LOCATIONS</div>
    <div class="locations__list">CEDAR RIDGE | MAPLE GROVE | HILLCREST | RIVERBEND | WESTBROOK</div>
    <div class="social" aria-label="Social media links"><span></span><span></span><span></span><span></span></div>
  </div>
</section>

</body>
</html>
```